Coralbay Yardcraft need a flyer - A6 - Double sided

We need a flyer that will engage potential customer in need for gardening services. We offer high quality gardening services spanning from lawn mowing and weeding to soil improvement to tree pruning and so on.
I would like a double sided flyer A6 size. I trust your expert touch in terms of lay out but the general idea I had was to have one side with the logo, a catchy picture (or more), the website/phone number/address and on the flip side a little more text focusing on the client perspective with statement such as 'Let us do the hard work so that you can enjoy your garden' (obviously the wording isn't my strongest skill) but the idea is to get into the customer perspective;
I would also like to list all the service we can offer such as but not limited to weeding, pruning, lawn care, green waste disposal, soil improvement, hedging, edging, lawn mowing,...
Happy for you to use any picture free of right from the internet if necessary

Target Market(s)

Home owner & Businesses

Industry/Entity Type

Landscape Gardening

Requirements
Must have
• website - http://yardcraft-coralbay.example.au (feel free to browse the website to get ideas on color theme and overall look)
• phone number - (08) 6193 4071
Nice to have
• a list of services on offer
• phone number and website
• being customer perspective focused (the benefits for the customer) - perhaps on the flip side some text like 'highly trained and experienced landscape gardeners so that the job is done perfectly every time', 'always carrying all range of commercial grade tools so that we can tackle any job', 'Experienced gardeners so that the job is achieve faster' (it doesn't have to be in those exact words as I trust that you may be expert in wording as well as designers?)

```html
<!DOCTYPE html>
<html lang="en">
<head>
<meta charset="utf-8">
<title>Coralbay Yardcraft – Gardening Services Flyer</title>
<link rel="stylesheet" href="https://fonts.googleapis.com/css2?family=Asap+Condensed:wght@600;700&family=Roboto+Condensed:wght@300;700&family=Open+Sans:wght@700&family=Give+You+Glory&display=swap">
<style>
  :root {
    --charcoal: #2e3132;
    --ink: #333333;
    --icon: #1b1b1b;
    --leaf: #7ac943;
    --paper-top: #efe5d8;
    --paper-bottom: #fbf8f4;
    --white: #ffffff;
  }
  * { margin: 0; padding: 0; box-sizing: border-box; }
  html, body { width: 850px; height: 1200px; overflow: hidden; }
  body { background: var(--white); font-family: "Roboto Condensed", sans-serif; }

  .flyer {
    position: relative;
    width: 850px;
    height: 1200px;
    overflow: hidden;
    background: linear-gradient(180deg, var(--paper-top) 0%, #f2eadf 60%, var(--paper-bottom) 100%);
  }

  .hero { position: absolute; left: 0; top: 0; width: 850px; height: 320px; }

  .brand-panel {
    position: absolute;
    left: 302px; top: 234px;
    width: 246px; height: 110px;
    background: var(--charcoal);
    display: flex; flex-direction: column; align-items: center; justify-content: center;
    color: var(--white);
    font-family: "Asap Condensed", sans-serif;
    font-weight: 700;
    text-transform: uppercase;
    line-height: 0.95;
    text-align: center;
  }
  .brand-panel .brand-line { font-size: 42px; letter-spacing: 0.5px; }

  .headline {
    position: absolute;
    top: 356px; left: 0; width: 850px;
    text-align: center;
    font-family: "Asap Condensed", sans-serif;
    font-weight: 700;
    font-size: 31px;
    letter-spacing: -0.5px;
    color: var(--ink);
  }

  .intro {
    position: absolute;
    top: 400px; left: 40px; width: 770px;
    text-align: center;
    font-family: "Give You Glory", cursive;
    font-size: 19px;
    line-height: 25px;
    color: var(--ink);
    white-space: nowrap;
  }

  .service {
    position: absolute;
    width: 240px;
    text-align: center;
  }
  .service .service-icon {
    display: block;
    margin: 0 auto;
    width: 130px; height: 100px;
    fill: var(--icon);
  }
  .service .service-label {
    margin-top: 10px;
    font-weight: 700;
    font-size: 15px;
    line-height: 19px;
    color: var(--ink);
    text-transform: uppercase;
  }

  .s-lawn   { left: 41px;  top: 540px; }
  .s-tree   { left: 314px; top: 540px; }
  .s-hedge  { left: 586px; top: 540px; }
  .s-organic{ left: 46px;  top: 692px; }
  .s-mulch  { left: 314px; top: 692px; }
  .s-weed   { left: 586px; top: 692px; }
  .s-waste  { left: 142px; top: 854px; }
  .s-soil   { left: 466px; top: 854px; }

  .phone {
    position: absolute;
    top: 1045px; left: 0; width: 850px;
    text-align: center;
    font-family: "Open Sans", sans-serif;
    font-weight: 700;
    font-size: 64px;
    letter-spacing: -2px;
    color: var(--charcoal);
  }

  .web-bar {
    position: absolute;
    top: 1142px; height: 13px;
    background: var(--leaf);
  }
  .web-bar.left { left: 0; width: 248px; }
  .web-bar.right { left: 602px; width: 248px; }

  .website {
    position: absolute;
    top: 1127px; left: 248px; width: 354px;
    text-align: center;
    font-weight: 300;
    font-size: 22px;
    letter-spacing: -0.5px;
    color: var(--ink);
    white-space: nowrap;
  }
</style>
</head>
<body>
<main class="flyer">
  <svg class="hero" viewBox="0 0 850 320" xmlns="http://www.w3.org/2000/svg">
    <defs>
      <linearGradient id="foliage" x1="0" y1="0" x2="0" y2="1">
        <stop offset="0" stop-color="#6f9a5a"/>
        <stop offset="0.45" stop-color="#3f6a30"/>
        <stop offset="1" stop-color="#2c4a22"/>
      </linearGradient>
      <clipPath id="hero-clip">
        <path d="M0,0 H850 V306 Q700,278 548,276 L300,276 Q150,266 0,262 Z"/>
      </clipPath>
    </defs>
    <g clip-path="url(#hero-clip)">
      <rect width="850" height="320" fill="url(#foliage)" role="img" aria-label="Photo of a smiling gardener in a high-visibility shirt trimming flowering shrubs under blue sky"/>
    </g>
    <path d="M0,262 Q150,266 300,276" fill="none" stroke="#2e3132" stroke-width="5"/>
    <path d="M548,276 Q700,278 850,306" fill="none" stroke="#2e3132" stroke-width="5"/>
    <path d="M60,280 Q180,272 300,288 L300,292 Q180,284 60,296 Z" fill="#7ac943"/>
    <path d="M548,280 Q700,282 850,310 L850,318 Q700,292 548,290 Z" fill="#7ac943"/>
  </svg>

  <div class="brand-panel">
    <span class="brand-line">Coralbay</span>
    <span class="brand-line">Yardcraft</span>
  </div>

  <h1 class="headline">LET US DO THE HARD WORK SO THAT YOU CAN ENJOY YOUR GARDEN</h1>

  <p class="intro">Thanks to our years of experience in landscaping, we have the skills and knowledge<br>required to deliver a consistently high quality service. We're here to work with you<br>both now, and in the long-term to help you achieve your garden paradise. Whether<br>you need simple weeding, pruning and garden maintenance or help transforming a<br>backyard jungle, you can trust us – your friendly local gardeners.</p>

  <section class="services">
    <div class="service s-lawn">
      <svg class="service-icon" viewBox="0 0 130 100" role="img" aria-label="Lawn mower icon">
        <path d="M70 48 L122 6 L126 11 L76 52 Z"/>
        <path d="M8 72 Q10 62 22 60 L58 58 Q66 50 74 50 L100 52 Q106 54 106 62 L106 82 L18 84 Q8 84 8 72 Z"/>
        <circle cx="28" cy="84" r="9" fill="#efe5d8" stroke="#1b1b1b" stroke-width="5"/>
        <circle cx="84" cy="82" r="11" fill="#efe5d8" stroke="#1b1b1b" stroke-width="5"/>
      </svg>
      <p class="service-label">Lawn Care</p>
    </div>
    <div class="service s-tree">
      <svg class="service-icon" viewBox="0 0 130 100" role="img" aria-label="Tree and spade icon">
        <path d="M45 8 L62 34 L54 34 L68 56 L58 56 L74 80 L16 80 L32 56 L22 56 L36 34 L28 34 Z"/>
        <rect x="41" y="80" width="8" height="14"/>
        <rect x="92" y="10" width="6" height="56"/>
        <path d="M84 6 H106 V14 H84 Z"/>
        <path d="M84 64 H106 V84 Q95 98 84 84 Z"/>
      </svg>
      <p class="service-label">Tree Pruning &amp; Plant Care</p>
    </div>
    <div class="service s-hedge">
      <svg class="service-icon" viewBox="0 0 130 100" role="img" aria-label="Hedge trimmer icon">
        <path d="M4 60 Q4 50 14 50 L30 50 L30 40 Q30 22 46 22 Q56 22 56 34 L56 50 L62 50 L62 86 L14 86 Q4 86 4 76 Z"/>
        <rect x="36" y="32" width="8" height="26" rx="4" fill="#efe5d8"/>
        <path d="M62 58 H118 Q128 58 128 68 Q128 78 118 78 H62 Z" fill="none" stroke="#1b1b1b" stroke-width="5"/>
      </svg>
      <p class="service-label">Hedge Trimming</p>
    </div>
    <div class="service s-organic">
      <svg class="service-icon" viewBox="0 0 130 100" role="img" aria-label="Seedling in soil icon">
        <rect x="62" y="34" width="6" height="36"/>
        <path d="M65 40 Q40 36 42 12 Q64 14 65 40 Z"/>
        <path d="M65 46 Q92 42 90 16 Q66 20 65 46 Z"/>
        <path d="M20 92 Q30 66 65 64 Q100 66 110 92 Z"/>
      </svg>
      <p class="service-label">Organic Gardening</p>
    </div>
    <div class="service s-mulch">
      <svg class="service-icon" viewBox="0 0 130 100" role="img" aria-label="Wood chipper icon">
        <path d="M4 44 L40 30 L50 60 L14 58 Z"/>
        <path d="M44 46 H92 V74 H44 Z"/>
        <path d="M74 46 Q72 14 104 12 L126 12 L126 20 L106 20 Q84 22 86 46 Z"/>
        <rect x="92" y="58" width="8" height="34"/>
        <circle cx="60" cy="80" r="11" fill="#efe5d8" stroke="#1b1b1b" stroke-width="6"/>
      </svg>
      <p class="service-label">Mulching</p>
    </div>
    <div class="service s-weed">
      <svg class="service-icon" viewBox="0 0 130 100" role="img" aria-label="Weeds and grass icon">
        <rect x="4" y="86" width="122" height="4"/>
        <g stroke="#1b1b1b" stroke-width="3" fill="none">
          <path d="M18 86 Q16 60 14 42"/><path d="M42 86 Q44 68 52 48"/>
          <path d="M64 86 Q64 60 70 42"/><path d="M88 86 Q92 50 104 30"/>
          <path d="M108 86 Q112 66 120 56"/><path d="M96 86 Q96 66 94 58"/>
          <path d="M28 86 L24 74 M32 86 L36 72 M56 86 L52 76 M76 86 L80 72 M116 86 L112 74"/>
        </g>
        <circle cx="14" cy="40" r="6"/><circle cx="52" cy="46" r="5"/>
        <circle cx="70" cy="40" r="6"/><circle cx="104" cy="28" r="7"/>
        <circle cx="120" cy="54" r="5"/><circle cx="94" cy="56" r="5"/>
      </svg>
      <p class="service-label">Weed Control</p>
    </div>
    <div class="service s-waste">
      <svg class="service-icon" viewBox="0 0 130 100" role="img" aria-label="Wheelie bin icon">
        <path d="M38 4 H94 V12 H38 Z"/>
        <path d="M40 14 H92 L86 92 H48 Z"/>
        <circle cx="84" cy="90" r="8" fill="#1b1b1b" stroke="#efe5d8" stroke-width="3"/>
      </svg>
      <p class="service-label">Rubbish &amp; Green<br>Waste Removal</p>
    </div>
    <div class="service s-soil">
      <svg class="service-icon" viewBox="0 0 130 100" role="img" aria-label="Flowers in a garden bed icon">
        <rect x="6" y="74" width="118" height="18"/>
        <g stroke="#1b1b1b" stroke-width="4">
          <path d="M36 74 V38 M66 74 V30 M96 74 V38"/>
        </g>
        <path d="M36 58 Q24 56 24 46 Q36 48 36 58 Z M66 52 Q80 50 80 40 Q66 42 66 52 Z M96 58 Q84 56 84 46 Q96 48 96 58 Z"/>
        <circle cx="36" cy="32" r="8"/><circle cx="66" cy="24" r="9"/><circle cx="96" cy="32" r="8"/>
        <circle cx="36" cy="32" r="3" fill="#efe5d8"/><circle cx="66" cy="24" r="3.5" fill="#efe5d8"/><circle cx="96" cy="32" r="3" fill="#efe5d8"/>
      </svg>
      <p class="service-label">Fertilising &amp; Soil<br>Improvement</p>
    </div>
  </section>

  <p class="phone">(08) 6193 4071</p>
  <span class="web-bar left"></span>
  <p class="website">www.Yardcraft-Coralbay.example.au</p>
  <span class="web-bar right"></span>
</main>
</body>
</html>
```